Business Card Design

We are a commercial real estate brokerage in San Francisco, leasing office buildings downtown.
I would like a clean, elegant look. Simple but powerful .

Industry/Entity Type

Business

Contact Information for Business Card

Derek Holloway
lic# 07258143
415.555.0172
derek@velt-commercial.example
velt-commercial.example

```html
<!DOCTYPE html>
<html lang="en">
<head>
<meta charset="utf-8">
<title>Velt Commercial – Business Card</title>
<link rel="stylesheet" href="https://fonts.googleapis.com/css2?family=Open+Sans:wght@400;600&family=Questrial&display=swap">
<style>
  :root {
    --backdrop: #0e0e0e;
    --card-front: #ffffff;
    --card-back: #f3f3f3;
    --accent-blue: #6b7fa0;
    --text-grey: #4f4f4f;
    --icon-grey: #6a7488;
    --mark-grey: #5a5a5a;
  }
  * { margin: 0; padding: 0; box-sizing: border-box; }
  html, body {
    width: 1200px; height: 900px; overflow: hidden;
    background: var(--backdrop);
  }
  .canvas { position: relative; width: 1200px; height: 900px; }

  .card {
    position: absolute;
    top: 306px;
    height: 271px;
    border-radius: 10px;
  }
  .card--front { left: 149px; width: 439px; background: var(--card-front); }
  .card--back  { left: 608px; width: 441px; background: var(--card-back); }

  .skyline-art {
    position: absolute;
    left: 27px; top: 76px;
    width: 168px; height: 110px;
    background: linear-gradient(180deg, #b9b9b9 0%, #7d7d7d 60%, #3c3c3c 100%);
    border-radius: 2px;
  }

  .contact {
    position: absolute;
    left: 218px; top: 80px;
    font-family: "Open Sans", sans-serif;
    color: var(--text-grey);
  }
  .contact__name {
    font-size: 15px; font-weight: 600;
    color: var(--accent-blue);
    line-height: 20px;
  }
  .contact__licence {
    margin-top: 10px;
    font-size: 12px; line-height: 16px;
  }
  .contact__list { list-style: none; margin-top: 13px; }
  .contact__item {
    display: flex; align-items: center;
    font-size: 12px; line-height: 16px;
  }
  .contact__icon {
    width: 9px; height: 9px;
    margin-right: 10px;
    fill: var(--icon-grey);
    flex: none;
  }

  .brand {
    position: absolute;
    left: 66px; top: 96px;
    display: flex; align-items: center;
    gap: 22px;
  }
  .brand__square {
    width: 64px; height: 64px;
    background: var(--mark-grey);
  }
  .brand__name {
    font-family: "Questrial", sans-serif;
    color: var(--accent-blue);
    line-height: 0.95;
    letter-spacing: 0.5px;
  }
  .brand__name-top { display: block; font-size: 52px; }
  .brand__name-bottom { display: block; font-size: 25px; margin-top: 4px; }
</style>
</head>
<body>
<main class="canvas">

  <section class="card card--front" aria-label="Card front">
    <div class="skyline-art" role="img" aria-label="Illustration of downtown office towers in greys"></div>
    <div class="contact">
      <p class="contact__name">Derek Holloway</p>
      <p class="contact__licence">Lic# 07258143</p>
      <ul class="contact__list">
        <li class="contact__item">
          <svg class="contact__icon" viewBox="0 0 10 10" aria-hidden="true"><path d="M2 0.5 L3.6 2.6 L2.8 3.6 C3.4 5 5 6.6 6.4 7.2 L7.4 6.4 L9.5 8 L8.4 9.5 C4.5 9.2 0.8 5.5 0.5 1.6 Z"/></svg>
          415.555.0172
        </li>
        <li class="contact__item">
          <svg class="contact__icon" viewBox="0 0 10 10" aria-hidden="true"><path d="M0.5 2 H9.5 V8 H0.5 Z M1 2.5 L5 5.5 L9 2.5" stroke="#fff" stroke-width="0.8"/></svg>
          derek@velt-commercial.example
        </li>
        <li class="contact__item">
          <svg class="contact__icon" viewBox="0 0 10 10" aria-hidden="true"><circle cx="5" cy="5" r="4.5"/><path d="M0.5 5 H9.5 M5 0.5 C3 3 3 7 5 9.5 M5 0.5 C7 3 7 7 5 9.5" stroke="#fff" stroke-width="0.6" fill="none"/></svg>
          velt-commercial.example
        </li>
      </ul>
    </div>
  </section>

  <section class="card card--back" aria-label="Card back">
    <div class="brand">
      <span class="brand__square" aria-hidden="true"></span>
      <p class="brand__name">
        <span class="brand__name-top">VELT</span>
        <span class="brand__name-bottom">COMMERCIAL</span>
      </p>
    </div>
  </section>

</main>
</body>
</html>
```